Business Card Design For Office Furniture Clearance Company

Kestrel Office Clearance - our company name pretty much explains what we do, we clear offices for high end clients, mainly plc's and large international companies.

We require a nice looking business card that displays professionalism but without being too serious.

It would be nice to see just a little more than a conventional boring business card, make sure you add some flare.

Industry/Entity Type

Office Furniture

Contact Information for Business Card

CARD 1

Mark Holloway
Director
mark@kestrelofficeclearance.co.uk
m: 07700 153928

t: 01632 960418
www.kestrelofficeclearance.co.uk

Kestrel Office Clearance
Unit K4 B
2-8 Fenwick Lane
Bletchley
Milton Keynes
ZZ9 4QT

free office clearances… you cant get better than that.

CARD 2

Peter Radford
Director
peter@kestrelofficeclearance.co.uk
m: 07700 382615

t: 01632 960418

Kestrel Office Clearance
Unit K4 B
2-8 Fenwick Lane
Bletchley
Milton Keynes
ZZ9 4QT

Font styles to use
Sans Serif

Requirements
Must have
• A white background - as we have a blue logo.
Nice to have
• Nice use of the logo - play around with this and dissect it.

```html
<!DOCTYPE html>
<html lang="en">
<head>
<meta charset="utf-8">
<title>Kestrel Office Clearance – Business Card</title>
<link rel="stylesheet" href="https://fonts.googleapis.com/css2?family=Source+Sans+3:ital,wght@0,400;0,600;1,400&display=swap">
<style>
  :root {
    --brand-blue: #0566a6;
    --card-paper: #e4e5e8;
    --backdrop: #d3d4d6;
    --ink-light: #ffffff;
    --ink-dark: #3f4043;
    --ring: #f2f3f5;
  }
  * { box-sizing: border-box; margin: 0; padding: 0; }
  html, body {
    width: 1105px; height: 1200px; overflow: hidden;
    background: var(--backdrop);
    font-family: "Source Sans 3", "Helvetica Neue", Arial, sans-serif;
  }
  .sheet { position: relative; width: 1105px; height: 1200px; }

  .card {
    position: absolute; left: 182px;
    width: 746px; height: 427px;
    background: var(--card-paper);
    overflow: hidden;
  }
  .card--front { top: 119px; }
  .card--back { top: 637px; }

  .card__art { position: absolute; inset: 0; width: 100%; height: 100%; }

  /* Front */
  .holder { position: absolute; left: 37px; top: 38px; color: var(--ink-light); }
  .holder__name { font-size: 27px; font-weight: 600; letter-spacing: 0.4px; line-height: 1; }
  .holder__role { font-size: 19px; font-weight: 400; letter-spacing: 0.3px; margin-top: 3px; }

  .address { position: absolute; left: 37px; top: 158px; color: var(--ink-light); font-size: 19.5px; line-height: 26px; font-style: normal; }
  .address__company { font-weight: 600; }

  .contacts { position: absolute; left: 37px; top: 279px; list-style: none; color: var(--ink-light); font-size: 18.5px; line-height: 28.5px; }
  .contacts li { display: flex; align-items: center; gap: 9px; }
  .contacts svg { width: 16px; height: 16px; flex: none; fill: var(--ink-light); }

  .brand-name {
    position: absolute; color: var(--ink-light);
    font-weight: 600; text-align: center; line-height: 1.1;
  }
  .brand-name--front { left: 405px; top: 170px; width: 300px; font-size: 34px; }
  .brand-name--back { left: 262px; top: 157px; width: 220px; font-size: 24px; }

  .tagline {
    position: absolute; left: 0; right: 0; top: 344px;
    text-align: center; font-style: italic; font-size: 19.5px; color: var(--ink-dark);
  }
</style>
</head>
<body>
<main class="sheet">

  <section class="card card--front" aria-label="Business card front">
    <svg class="card__art" viewBox="0 0 746 427" aria-hidden="true">
      <rect x="0" y="0" width="530" height="427" fill="var(--brand-blue)"/>
      <circle cx="533" cy="213" r="214" fill="var(--brand-blue)" stroke="var(--ring)" stroke-width="3"/>
    </svg>

    <header class="holder">
      <p class="holder__name">MARK HOLLOWAY</p>
      <p class="holder__role">DIRECTOR</p>
    </header>

    <address class="address">
      <p class="address__company">Kestrel Office Clearance</p>
      <p>Unit K4 B, 2-8 Fenwick Lane</p>
      <p>Harlow Vale, Northbridge</p>
      <p>ZZ9 4QT</p>
    </address>

    <ul class="contacts">
      <li>
        <svg viewBox="0 0 16 16" aria-hidden="true"><path d="M3.2 1.5l2.2 2.6-1.3 1.8c.9 2 2.3 3.5 4.2 4.4l1.8-1.3 2.6 2.2-1 2.3C6.8 13.6 2.4 9.2 1 3.3z"/></svg>
        <span>01632 960418</span>
      </li>
      <li>
        <svg viewBox="0 0 16 16" aria-hidden="true"><path d="M4.5 0.5h7a1 1 0 0 1 1 1v13a1 1 0 0 1-1 1h-7a1 1 0 0 1-1-1v-13a1 1 0 0 1 1-1zm.6 2v9.5h5.8V2.5zM8 13a.8.8 0 1 0 0 1.6A.8.8 0 0 0 8 13z" fill-rule="evenodd"/></svg>
        <span>07700 153928</span>
      </li>
      <li>
        <svg viewBox="0 0 16 16" aria-hidden="true"><path d="M1 3.5h14v9H1z"/><path d="M1.6 4.2L8 9l6.4-4.8" stroke="var(--brand-blue)" stroke-width="1.2" fill="none"/></svg>
        <span>mark@kestrelofficeclearance.co.uk</span>
      </li>
      <li>
        <svg viewBox="0 0 16 16" aria-hidden="true"><circle cx="8" cy="8" r="7"/><path d="M5 4.5c1.5.3 2 1.6 1.2 2.6-.8.9.3 2 1.4 2.2.8.2.6 1.8-.2 2.7M10.5 3.6c-.7 1-.2 2 .9 2.2 1 .2 1.6 1 1.5 2" stroke="var(--brand-blue)" stroke-width="1.3" fill="none"/></svg>
        <span>www.kestrelofficeclearance.co.uk</span>
      </li>
    </ul>

    <p class="brand-name brand-name--front">Kestrel<br>Office Clearance</p>
  </section>

  <section class="card card--back" aria-label="Business card back">
    <svg class="card__art" viewBox="0 0 746 427" aria-hidden="true">
      <circle cx="372" cy="184" r="115" fill="var(--brand-blue)"/>
    </svg>
    <p class="brand-name brand-name--back">Kestrel<br>Office Clearance</p>
    <p class="tagline">Free office clearances… you cant get better than that.</p>
  </section>

</main>
</body>
</html>
```